Blow Dry Bar Business Cards

These cards must be eye catching and modern.
You must be willing to work fast and make changes.

Winner will be offered other projects

Files 1 THIS IS THE STYLE CARDS I AM INTRESTED IN!!!
Please be creative, I am paying for my own eye catching design. I need files to be nexa press ready.

COLORS THAT ARE PAINTED INSIDE MY SHOP:
- - - http://www.quorvelpaint.example/en/explore-colors/painter/color-selector.html?colors=4007-3C

- - - http://www.brandivex.example/color/paint-colors/hidden-corridor-d58-2

I want the business cards sleek and modern if you use the logo please correct imperfections. I added the part that says Blow Dry Bar (see website).
Do not be afraid to separate the blow dryer from the name to make the cards look like the file with the pink elephant.

SHOULD INCLUDE
*Blow Dryer (we are a blow dry bar not a salon we do not cut or color so do not include sheers of any kind)
*BUSINESS NAME: Simply Swept Upward - Blow Dry Bar (PLEASE SEE MY WEBSITE)
* Website: SIMPLYSWEPTUPWARD.EXAMPLE
*Phone number (555) 014-2763
Updates

Nexa press said it can be submitted in JPG

http://www.brandivex.example/color/paint-colors/hidden-corridor-d58-2 http://www.quorvelpaint.example/en/explore-colors/painter/color-selector.html?colors=4007-3C ^^^^ These links will take you to the color paint that is painted inside my shop.

Target Market(s)

AGES 18 - 55 WOMEN
HIGH END MARKET

Industry/Entity Type

Salon

Requirements
Must have
• SEE COLOR EXAMPLE FILE
BLOW DRYER
UNIQUE
I LIKE THE CARD WITH THE PINK ELEPHANT THE BEST
Nice to have
• BE AS CREATIVE AND MODERN AS POSSIBLE DO NOT COPY ANY OF THE CARDS BELOW.
Should not have
• SCISSORS
PINK

```html
<!DOCTYPE html>
<html lang="en">
<head>
<meta charset="utf-8">
<title>Simply Swept Upward – Business Cards</title>
<link rel="stylesheet" href="https://fonts.googleapis.com/css2?family=Open+Sans:wght@400;800&display=swap">
<style>
  :root {
    --backdrop: #e9e6e1;
    --card-light: #efefef;
    --card-dark: #474747;
    --ink-dark: #3f3f3f;
    --ink-on-dark: #2a2a2a;
    --crease: #c9c9c9;
  }
  * { margin: 0; padding: 0; box-sizing: border-box; }
  html, body {
    width: 1200px;
    height: 900px;
    overflow: hidden;
    background: var(--backdrop);
    font-family: "Open Sans", Arial, sans-serif;
  }
  .sheet {
    position: relative;
    width: 1200px;
    height: 900px;
  }
  .card {
    position: absolute;
    left: 250px;
    width: 700px;
    height: 400px;
    border-radius: 28px;
    box-shadow: 0 6px 18px rgba(0,0,0,0.18);
    overflow: hidden;
  }

  /* Front: brand half + contact half */
  .card--front {
    top: 40px;
    background: var(--card-light);
    display: flex;
  }
  .card__half {
    width: 50%;
    height: 100%;
    position: relative;
  }
  .card__half--brand {
    border-right: 2px solid var(--crease);
  }
  .brand {
    position: absolute;
    left: 50px;
    right: 30px;
    top: 150px;
    color: var(--ink-dark);
  }
  .brand__row {
    display: flex;
    align-items: center;
    gap: 16px;
  }
  .brand__dot {
    width: 22px;
    height: 22px;
    border-radius: 50%;
    background: var(--ink-dark);
    flex: none;
  }
  .brand__name {
    font-weight: 800;
    font-size: 40px;
    line-height: 1.05;
  }
  .brand__tagline {
    margin-top: 10px;
    padding-left: 38px;
    font-weight: 400;
    font-size: 24px;
    line-height: 1;
    white-space: nowrap;
  }
  .contact {
    position: absolute;
    left: 48px;
    top: 120px;
    list-style: none;
    color: var(--ink-dark);
    font-size: 17px;
    font-weight: 400;
    text-transform: uppercase;
    letter-spacing: 0.04em;
    line-height: 1.45;
    white-space: nowrap;
  }
  .contact__phone { margin-bottom: 2px; }
  .contact__web { margin-bottom: 10px; }

  /* Back: tone-on-tone name */
  .card--back {
    top: 460px;
    background: var(--card-dark);
  }
  .back-brand {
    position: absolute;
    left: 40px;
    top: 150px;
    color: var(--ink-on-dark);
  }
  .back-brand__row {
    display: flex;
    align-items: center;
    gap: 20px;
  }
  .back-brand__dot {
    width: 30px;
    height: 30px;
    border-radius: 50%;
    background: var(--ink-on-dark);
    flex: none;
  }
  .back-brand__name {
    font-weight: 800;
    font-size: 50px;
    line-height: 1;
    letter-spacing: -0.01em;
    white-space: nowrap;
  }
  .back-brand__tagline {
    margin-top: 14px;
    padding-left: 240px;
    font-weight: 400;
    font-size: 40px;
    line-height: 1;
    white-space: nowrap;
  }
</style>
</head>
<body>
  <main class="sheet">
    <section class="card card--front" aria-label="Card front">
      <div class="card__half card__half--brand">
        <div class="brand">
          <div class="brand__row">
            <span class="brand__dot"></span>
            <span class="brand__name">Simply Swept<br>Upward</span>
          </div>
          <p class="brand__tagline">blow dry bar</p>
        </div>
      </div>
      <div class="card__half card__half--info">
        <ul class="contact">
          <li class="contact__phone">(555) 014 - 2763</li>
          <li class="contact__web">SIMPLYSWEPTUPWARD.EXAMPLE</li>
          <li>27 Harbor Mill Road Suite</li>
          <li>4 Fenwick Bay, Texas 77000</li>
        </ul>
      </div>
    </section>

    <section class="card card--back" aria-label="Card back">
      <div class="back-brand">
        <div class="back-brand__row">
          <span class="back-brand__dot"></span>
          <span class="back-brand__name">Simply Swept Upward</span>
        </div>
        <p class="back-brand__tagline">blow dry bar</p>
      </div>
    </section>
  </main>
</body>
</html>
```